Flyer for a Unique Type of Tax Services

Please refer to the attached sample design for reference. Feel free to change the wording as needed. Here is the project brief:

Objective:
Objective of this flyer is to introduce our services which we are launching soon, which is new of a kind, to our potential customers i.e. online tax return preparation. By looking at the flyer we want our target audience to get convinced of our services and visit our website and register with us. They don’t have to pay anything to register.

Our Competitors:
Currently there are three main options available to get tax returns prepared. First is to buy tax software and get tax return prepared at own, this is the cheapest option. There are studies that suggest that people who are not well aware of tax laws there are chances they miss certain tax refunds by filing returns at their own and potentially lose money. Second option is to go to the local offices of nation-wide tax service companies like P&L Fenwick and Morrow Quillan. They open offices only during tax season i.e. Jan through April but they are not available other part of the year and their association with the customers is temporary. Third option is to go to a CPA office which are the most expensive and very few people go for this option.

Weaknesses of the Current Options:
By self-preparing tax returns, there are chances that one can overlook certain tax laws that can provide additional tax credits and exemptions to people and overall they could have got a higher tax refund from the Govt. but they may miss it.
By going to other competitors during the peak time when tax returns are due, there are high chances that they don't have enough time to do research to ensure maximum refunds based on the exact circumstances of the individuals at the peak time as many people come to them during that time. Also they are not available after the tax season to provide them any answers to their questions or provide them tax planning tips to help them save tax in the next season.
By going to the CPA office, they charge a lot of fees and also for any tax advice later during the year, they will charge additional fees.

What we are offering:
We are offering a new option i.e. online tax return preparation through experts. We'll charge the fees competitive to what people are paying to local tax providers. But we will be different than our competitors as we'll be providing value added service if they got their returns prepared through us. Value added services we will be free of any additional cost for our customers who'll get tax return prepared through us.

Our Target Audience:
Our target audience is any person or couple who go to the tax service providers like P&L Fenwick or Morrow Quillan to get their tax returns prepared.

How We are Different:
Here is the summary of the unique aspects of our business as compared to the competitors:
- Customers just pay us the price for preparing the annual return and price is comparable and competitive to what they have been paying to other providers.
- Unlike our competitors, we do extensive research to review the circumstances of our customers and explore applicable tax laws to make sure all available tax credits, exemptions, and deductions are taken for our customers, whereas our customers don't usually do such kind of research as during the peak tax season when customers approach them they usually don’t have time to do that kind of research. We start our association with our customers much sooner than the actual due date and this provides us time to do extensive research and we try our best that our customers could get higher tax returns.
- By just getting tax returns prepared through us, we enter into a long-term association with our customers and provide them complimentary tax planning tips throughout the year to help them save tax in the following year
- We are available to our customers year-round to provide complementary answers to any tax related questions without any additional cost e.g. how to save tax when buying a car, whether to buy or lease the care to save tax, for the sole-proprietor business how to save tax by using portion of the home as home-office, how to save tax by using personal car for personal business.
- We also provide answers to other basic financial advise related matters e.g. which insurance product is better, whether full insurance or term-life insurance to chose, how to save for the retirement etc.

Other Details:
Our logo has already been designed and we want the same logo to be used in the flyer. Our website address is: www.LedgerPilotHub.com (it is still under construction but to get perspective of what we are trying to offer, visit this alternate website that it not final yet but will give an idea: http://www.ledgerpilothub.com/wordpress. Fyi, a video at this link is only a placeholder and not relevant to our services)

Requirements
Must have
• Please refer to the sample flyer attached. Feel free to change the design and language.
Should not have
• Please do not put any testimonial on the flyer as reflected in the under construction website.

```html
<!DOCTYPE html>
<html lang="en">
<head>
<meta charset="utf-8">
<title>LedgerPilot Hub – Online Tax Return Preparation</title>
<link rel="stylesheet" href="https://fonts.googleapis.com/css2?family=Varela+Round&family=Montserrat:ital,wght@0,400;0,600;1,600&display=swap">
<style>
  :root{
    --navy:#2c4a98;
    --orange:#f08a24;
    --teal:#5bc1c4;
    --stone:#5a5a5a;
    --stone-light:#8a8a8a;
    --ink:#222222;
    --footer:#d8d8d8;
    --white:#ffffff;
  }
  html,body{margin:0;padding:0;overflow:hidden;}
  body{background:var(--white);}
  .flyer{
    position:relative;width:745px;height:1200px;overflow:hidden;
    background:var(--white);font-family:"Montserrat",sans-serif;color:var(--ink);
  }
  .hero{position:absolute;left:0;top:0;width:745px;height:480px;}
  .headline{
    position:absolute;left:0;top:502px;width:745px;margin:0;text-align:center;
    font-family:"Varela Round",sans-serif;font-weight:400;font-size:29px;line-height:39px;
    color:var(--navy);
  }
  .headline strong{font-weight:400;-webkit-text-stroke:0.6px var(--navy);}
  .questions{position:absolute;left:0;top:660px;width:745px;margin:0;padding:0;list-style:none;}
  .questions li{
    position:relative;padding:0 20px 0 30px;margin-bottom:26px;
    font-size:16.5px;line-height:25px;
  }
  .questions li::before{
    content:"";position:absolute;left:14px;top:9px;width:7px;height:7px;
    background:var(--orange);box-shadow:inset 0 0 0 2px var(--navy);
  }
  .questions strong,.offer strong{font-weight:600;}
  .offer{
    position:absolute;left:20px;top:850px;width:705px;margin:0;text-align:center;
    font-size:16.5px;line-height:26px;
  }
  .offer em{color:var(--orange);font-weight:600;}
  .register{
    position:absolute;left:0;top:927px;width:745px;margin:0;text-align:center;
    font-size:18px;line-height:26px;
  }
  .register em{color:var(--orange);font-weight:600;margin-right:6px;}
  .register a{color:var(--navy);font-weight:600;text-decoration:none;}
  .register a .accent{color:var(--orange);}
  .brand{
    position:absolute;left:0;top:992px;width:745px;text-align:center;
    font-family:"Montserrat",sans-serif;font-weight:600;font-size:30px;color:var(--navy);
    letter-spacing:0.5px;
  }
  .brand::before{
    content:"";display:inline-block;width:14px;height:14px;border-radius:50%;
    background:var(--orange);margin-right:10px;vertical-align:middle;position:relative;top:-3px;
  }
  .footer-band{position:absolute;left:0;top:1040px;width:745px;height:160px;}
  .footer-text{
    position:absolute;left:30px;top:1086px;width:688px;margin:0;
    font-size:16.5px;line-height:26px;text-align:justify;color:var(--ink);
  }
</style>
</head>
<body>
<main class="flyer">
  <svg class="hero" viewBox="0 0 745 480" aria-hidden="false">
    <defs>
      <linearGradient id="stoneWall" x1="0" y1="0" x2="1" y2="1">
        <stop offset="0" stop-color="var(--stone-light)"/>
        <stop offset="0.6" stop-color="var(--stone)"/>
        <stop offset="1" stop-color="#4a4a4a"/>
      </linearGradient>
    </defs>
    <polygon class="hero-photo" role="img" aria-label="Smiling woman holding a blue umbrella against a grey wall with falling 'tax' words"
      points="0,0 745,0 745,232 300,463 0,398" fill="url(#stoneWall)"/>
    <polygon class="hero-band" points="0,355 300,424 745,115 745,232 300,463 0,398" fill="var(--teal)" opacity="0.85"/>
    <polygon class="hero-stripe" points="0,398 300,463 745,232 745,240 300,471 0,406" fill="var(--orange)"/>
  </svg>

  <h1 class="headline">Does your Tax Return Preparer<br>has time to do extensive research<br>for you to get <strong>MAXIMUM REFUNDS?</strong></h1>

  <ul class="questions">
    <li>Do you get <strong>Year-Round Free Advice</strong> regarding your Tax Related Questions from your existing Tax Service Provider?</li>
    <li>Does your existing <strong>Tax Service Provider</strong> give you <strong>Complementary Tax Planning Tip</strong>s throughout the year to help you save tax in the following financial year?</li>
  </ul>

  <p class="offer"><em>If not,</em> then try us as we do provide all these services year-round to our customers who get tax returns prepared through us at no additional COST.</p>

  <p class="register"><em>Register now free at:</em> <a href="http://www.ledgerpilothub.com">www.<span class="accent">LedgerPilot</span>Hub.com</a></p>

  <div class="brand">LedgerPilot Hub</div>

  <svg class="footer-band" viewBox="0 0 745 160" aria-hidden="true">
    <rect x="0" y="22" width="745" height="138" fill="var(--footer)"/>
    <polygon points="220,0 530,0 220,42" fill="var(--white)"/>
  </svg>

  <p class="footer-text">And right away we'll start doing research for you and will be available year-round to answer your tax related queries and we will keep providing you tax planning tips and also provide you guideline on other financial planning matters.</p>
</main>
</body>
</html>
```